New Innovative Counselling and psychotherapy Service needs Business Card design

Keep it simple and professional. On one side, just company name and logo (perhaps in all blue) and maybe a tag line.

On other side (all white) my name and Qualifications in centre

Industry/Entity Type

Health And Wellness

Contact Information for Business Card

Dara Whelby
Counsellor & Psychotherapist
BSc (Psychol.), BA, Dip. (Couns. & Psych.), PG.Cert (CBT), FGTrK, ONRE

I will also require Mobile no, Email and web site address of which I'll pass on to final designer.

Font styles to use
Sans Serif

Requirements
Must have
• My Logo Only and please use the colours in logo that is in it.
Should not have
• Any other images

```html
<!DOCTYPE html>
<html lang="en">
<head>
<meta charset="utf-8">
<title>Thrive Lane – Business Card</title>
<link href="https://fonts.googleapis.com/css2?family=Montserrat:wght@300;400;500;600&display=swap" rel="stylesheet">
<style>
  :root {
    --backdrop: #3a3532;
    --card: #1b1b1c;
    --card-edge: #3d8fc4;
    --blue: #46a9e0;
    --green: #7cc242;
    --ink: #f2f2f2;
    --muted: #d8d8d8;
  }
  * { box-sizing: border-box; margin: 0; padding: 0; }
  html, body {
    width: 1200px; height: 715px; overflow: hidden;
    background: var(--backdrop);
    font-family: "Montserrat", sans-serif;
    color: var(--ink);
  }
  .stage {
    position: relative; width: 1200px; height: 715px;
    display: flex; align-items: center; justify-content: center; gap: 50px;
  }
  .card {
    position: relative; width: 525px; height: 300px;
    background: var(--card);
    border-radius: 6px;
    box-shadow: 0 10px 24px rgba(0,0,0,.45);
  }
  /* Front */
  .card--front { border-bottom: 5px solid var(--card-edge); }
  .front-brand {
    position: absolute; left: 0; right: 0; top: 96px;
    display: flex; align-items: center; justify-content: center; gap: 14px;
  }
  .brand-dot { width: 30px; height: 30px; border-radius: 50%; background: var(--blue); }
  .front-brand .brand-name {
    font-size: 34px; font-weight: 300; color: var(--blue); letter-spacing: .5px;
  }
  .front-url {
    position: absolute; left: 0; right: 0; bottom: 40px; text-align: center;
    font-size: 13px; font-weight: 400; color: var(--ink);
  }
  .url-domain { color: var(--green); }
  /* Back */
  .back-brand {
    position: absolute; left: 34px; top: 118px;
    display: flex; align-items: center; gap: 10px;
  }
  .back-brand .brand-dot { width: 20px; height: 20px; }
  .back-brand .brand-name { font-size: 21px; font-weight: 300; color: var(--ink); }
  .divider {
    position: absolute; left: 262px; top: 70px; width: 2px; height: 160px;
    background: var(--green);
  }
  .details { position: absolute; left: 282px; top: 66px; right: 20px; }
  .person-name {
    font-size: 24px; font-weight: 600; color: var(--blue); text-transform: uppercase;
    letter-spacing: .3px; line-height: 1.1;
  }
  .role, .quals { font-size: 12px; line-height: 1.4; color: var(--muted); }
  .contacts { list-style: none; margin-top: 12px; }
  .contacts li {
    display: flex; align-items: center; gap: 8px;
    font-size: 13px; line-height: 1.55; color: var(--ink);
  }
  .contacts svg { width: 10px; height: 10px; flex: none; }
</style>
</head>
<body>
<main class="stage">
  <section class="card card--front" aria-label="Card front">
    <div class="front-brand">
      <span class="brand-dot"></span>
      <span class="brand-name">Thrive Lane</span>
    </div>
    <p class="front-url">www.<span class="url-domain">thrivelane</span>.com</p>
  </section>

  <section class="card card--back" aria-label="Card back">
    <div class="back-brand">
      <span class="brand-dot"></span>
      <span class="brand-name">Thrive Lane</span>
    </div>
    <div class="divider"></div>
    <div class="details">
      <h1 class="person-name">Dara Whelby</h1>
      <p class="role">Counsellor &amp; Psychotherapist</p>
      <p class="quals">BSc (Psychol.), BA, Dip. (Couns. &amp; Psych.), PG.Cert (CBT), FGTrK, ONRE</p>
      <ul class="contacts">
        <li>
          <svg viewBox="0 0 10 10" aria-hidden="true"><path d="M2 1 L4 1 L4.6 3 L3.4 3.8 Q4.4 5.8 6.2 6.6 L7 5.4 L9 6 L9 8 Q5 9 2.4 6 Q1 4 2 1Z" fill="var(--blue)"/></svg>
          888-555-0147
        </li>
        <li>
          <svg viewBox="0 0 10 10" aria-hidden="true"><rect x="1" y="2" width="8" height="6" fill="none" stroke="var(--blue)" stroke-width="1"/><path d="M1 2 L5 5.5 L9 2" fill="none" stroke="var(--blue)" stroke-width="1"/></svg>
          info@thrivelane.com
        </li>
        <li>
          <svg viewBox="0 0 10 10" aria-hidden="true"><circle cx="5" cy="5" r="4" fill="none" stroke="var(--blue)" stroke-width="1"/><path d="M1 5 H9 M5 1 Q2.5 5 5 9 M5 1 Q7.5 5 5 9" fill="none" stroke="var(--blue)" stroke-width=".8"/></svg>
          www.<span class="url-domain">thrivelane</span>.com
        </li>
      </ul>
    </div>
  </section>
</main>
</body>
</html>
```